Tall Fern Roofing Business Card

Need a business card with the logo that was designed here

Contact Information for Business Card

Name, Title, Phone, Email, Website, Company name

```html
<!DOCTYPE html>
<html lang="en">
<head>
<meta charset="utf-8">
<title>Tall Fern Roofing – Business Card</title>
<link rel="stylesheet" href="https://fonts.googleapis.com/css2?family=Montserrat:wght@400;500;700&display=swap">
<style>
  :root {
    --page: #ebebeb;
    --card-front: #818081;
    --front-ink: #c9c9c9;
    --card-back: #ffffff;
    --brand-blue: #3c6fbc;
    --ink-grey: #6f6f70;
    --ink-dark: #333333;
    --band-grey: #808080;
  }
  * { box-sizing: border-box; margin: 0; padding: 0; }
  html, body { width: 1200px; height: 900px; overflow: hidden; }
  body {
    background: var(--page);
    font-family: "Montserrat", sans-serif;
    position: relative;
  }
  .card {
    position: absolute;
    left: 280px;
    width: 640px;
    height: 366px;
    box-shadow: 0 6px 18px rgba(0,0,0,0.12);
    overflow: hidden;
  }
  .card--front { top: 60px; background: var(--card-front); }
  .card--back { top: 474px; background: var(--card-back); }

  .wordmark {
    display: flex;
    align-items: center;
    gap: 12px;
    font-weight: 700;
    letter-spacing: 0.5px;
  }
  .wordmark__square { width: 16px; height: 16px; flex: none; }

  .card--front .wordmark {
    position: absolute;
    left: 50%; top: 50%;
    transform: translate(-50%, -50%);
    font-size: 36px;
    color: var(--front-ink);
    white-space: nowrap;
  }
  .card--front .wordmark__square { width: 22px; height: 22px; background: var(--front-ink); }

  .card--back .wordmark {
    position: absolute;
    right: 44px; top: 52px;
    font-size: 24px;
    color: var(--brand-blue);
  }
  .card--back .wordmark__square { background: var(--brand-blue); }

  .person { position: absolute; left: 46px; top: 150px; }
  .person__name { font-size: 23px; font-weight: 700; letter-spacing: 1px; color: var(--ink-grey); }
  .person__first { color: var(--brand-blue); }
  .person__title { font-size: 15px; color: var(--ink-dark); margin-top: 2px; }

  .divider {
    position: absolute; left: 46px; right: 44px; top: 212px;
    height: 1px; background: var(--brand-blue);
  }

  .contacts { position: absolute; left: 46px; top: 228px; list-style: none; }
  .contacts li {
    display: flex; align-items: center; gap: 10px;
    font-size: 15px; color: var(--ink-dark); line-height: 26px;
  }
  .contacts svg { width: 14px; height: 14px; flex: none; }

  .address {
    position: absolute; right: 44px; top: 228px;
    text-align: right; font-size: 15px; line-height: 22px; color: var(--ink-dark);
    font-style: normal;
  }

  .bands { position: absolute; left: 0; bottom: 0; width: 640px; height: 40px; }
</style>
</head>
<body>

<section class="card card--front" aria-label="Card front">
  <div class="wordmark"><span class="wordmark__square"></span>Tall Fern Roofing</div>
</section>

<section class="card card--back" aria-label="Card back">
  <div class="wordmark"><span class="wordmark__square"></span>Tall Fern Roofing</div>

  <div class="person">
    <p class="person__name"><span class="person__first">DECLAN</span> MARSH</p>
    <p class="person__title">Managing Director</p>
  </div>

  <div class="divider"></div>

  <ul class="contacts">
    <li>
      <svg viewBox="0 0 14 14" aria-hidden="true"><circle cx="7" cy="7" r="7" fill="var(--brand-blue)"/><path d="M4.5 3.5l1.5 0 .6 1.8-.9.7a5 5 0 0 0 2.3 2.3l.7-.9 1.8.6v1.5c-3.5.3-6.3-2.5-6-6z" fill="#fff"/></svg>
      0400 555 172
    </li>
    <li>
      <svg viewBox="0 0 14 14" aria-hidden="true"><circle cx="7" cy="7" r="7" fill="var(--brand-blue)"/><rect x="3.5" y="4.5" width="7" height="5" fill="#fff"/><path d="M3.5 4.5L7 7.3 10.5 4.5" stroke="var(--brand-blue)" stroke-width="0.9" fill="none"/></svg>
      info@tallfernroofing.com
    </li>
    <li>
      <svg viewBox="0 0 14 14" aria-hidden="true"><circle cx="7" cy="7" r="7" fill="var(--brand-blue)"/><circle cx="7" cy="7" r="3.6" fill="none" stroke="#fff" stroke-width="1"/><path d="M3.4 7h7.2M7 3.4c-1.6 2-1.6 5.2 0 7.2M7 3.4c1.6 2 1.6 5.2 0 7.2" stroke="#fff" stroke-width="0.8" fill="none"/></svg>
      www.tallfernroofing.com
    </li>
  </ul>

  <address class="address">
    418 Wattle Grove Road<br>
    Kestrel County Name 5180
  </address>

  <svg class="bands" viewBox="0 0 640 40" aria-hidden="true">
    <polygon points="0,30 380,30 370,40 0,40" fill="var(--brand-blue)"/>
    <polygon points="398,22 640,22 640,40 386,40" fill="var(--band-grey)"/>
  </svg>
</section>

</body>
</html>
```